Kestrova - presentation for a remote DBA team offering data platform management

We need a website design for wordpress site called Kestrova.cz
We deliver remote database and data platform administration and development, oversee the database administrators, consult and train the personnel responsible for the database operations. The website should include several sections, home page with graphics elements supporting the name and service - remote dba work; blog section; service introduction and description, team introduction and description, download section for documents, presentations etc.

Target Market(s)

small and medium business companies requiring remote DBA service

Number of Pages Required

3 page

Font styles to use
Sans Serif

Colors

Designer to choose colors to be used in the design.

Requirements
Must have
• The website should have several sections to introduce the services, blog, team introduction, downloads

```html
<!DOCTYPE html>
<html lang="en">
<head>
<meta charset="utf-8">
<title>Kestrova.cz – Remote DBA</title>
<link rel="stylesheet" href="https://fonts.googleapis.com/css2?family=Montserrat:wght@400;500;600;700;800&family=Lato:wght@400;700&family=Libre+Baskerville:ital@0;1&family=EB+Garamond:wght@500&display=swap">
<style>
:root{
  --purple:#6a3cf4;
  --purple-deep:#5a2fe0;
  --blue:#4f6cf0;
  --ink:#2b2b33;
  --text:#5d5d66;
  --muted:#8a8a94;
  --white:#ffffff;
  --dark:#1e1f24;
  --rule:rgba(255,255,255,.28);
}
*{box-sizing:border-box;margin:0;padding:0}
html,body{width:1200px;height:3191px;overflow:hidden}
body{position:relative;background:var(--white);font-family:'Lato',Arial,sans-serif;color:var(--text)}
.abs{position:absolute}

/* hero */
.hero{left:0;top:0;width:1200px;height:666px;background:linear-gradient(160deg,#4a4d56 0%,#2c2e35 45%,#3b3d45 70%,#23242a 100%)}
.nav{left:0;top:0;width:1200px;height:86px}
.logo{left:79px;top:26px;font-family:'Montserrat',sans-serif;font-weight:600;font-size:28px;color:var(--white);letter-spacing:.2px}
.menu{right:79px;top:34px;display:flex;gap:40px;font-family:'Montserrat',sans-serif;font-size:14px;font-weight:500;color:var(--white);letter-spacing:.3px}
.menu span{position:relative}
.menu .active::before{content:"";position:absolute;left:-4px;right:-4px;top:-20px;height:3px;background:var(--purple)}
.hero-tag{left:0;width:1200px;top:240px;text-align:center;font-family:'Libre Baskerville',serif;font-style:italic;font-size:34px;color:var(--white)}
.hero-title{left:0;width:1200px;top:304px;text-align:center;font-family:'Montserrat',sans-serif;font-weight:600;font-size:48px;color:var(--white)}

/* callout boxes */
.stack{background:rgba(255,255,255,.35)}
.callout{background:var(--white);box-shadow:0 14px 34px rgba(0,0,0,.12);display:flex;align-items:center;justify-content:space-between;padding:0 36px 0 54px}
.callout p{font-family:'EB Garamond',serif;font-weight:500;font-size:31px;line-height:44px;color:var(--ink)}
.btn{display:inline-flex;align-items:center;justify-content:center;gap:14px;background:var(--purple);color:var(--white);border-radius:26px;font-family:'Montserrat',sans-serif;font-weight:600;font-size:19px;letter-spacing:.3px;box-shadow:0 8px 18px rgba(106,60,244,.35)}

/* about */
.about-media{left:79px;top:830px;width:500px;height:302px;border-radius:14px;background:linear-gradient(150deg,#3a3c44 0%,#1c1d22 60%,#50535c 100%)}
.grad-title{font-family:'Montserrat',sans-serif;font-weight:800;font-size:38px;background:linear-gradient(90deg,var(--purple) 0%,var(--blue) 100%);-webkit-background-clip:text;background-clip:text;color:transparent}
.about-title{left:636px;top:818px}
.about-copy{left:636px;top:870px;width:490px;font-size:14px;line-height:25px;color:var(--text)}
.about-copy p+p{margin-top:10px}

/* services & team band */
.band{left:0;top:1219px;width:1200px;height:711px;background:var(--purple)}
.section-title{left:0;width:1200px;text-align:center;font-family:'Montserrat',sans-serif;font-weight:700;font-size:36px;color:var(--white);letter-spacing:.5px}
.service{width:340px;text-align:center;color:var(--white)}
.service svg{display:block;margin:0 auto}
.service h3{margin-top:26px;font-family:'Montserrat',sans-serif;font-weight:500;font-size:21px}
.service p{margin-top:10px;font-size:14.5px;line-height:24px;opacity:.9}
.band-rule{left:79px;top:1611px;width:1042px;height:1px;background:var(--rule)}

.member{width:238px;text-align:center}
.member .photo{width:238px;height:261px}
.member h4{margin-top:26px;font-family:'Montserrat',sans-serif;font-weight:500;font-size:21px;color:#4a4a52}
.member p{margin-top:10px;font-size:14px;color:var(--text)}

/* blog */
.post{width:321px;text-align:center}
.post .img{width:321px;height:229px}
.post .date{position:relative;margin:-40px auto 0;width:236px;height:42px;background:var(--white);font-family:'Montserrat',sans-serif;font-size:16px;color:#3a3a42;line-height:50px}
.post p{margin-top:10px;font-size:14px;line-height:24px;color:var(--text);padding:0 40px}

/* footer */
.footer-bg{left:0;top:2753px;width:1200px;height:375px;background:linear-gradient(160deg,#2a2b31 0%,#16171b 55%,#2c2d33 100%)}
.newsletter-field{left:319px;top:2960px;width:560px;height:41px;border-bottom:1px solid rgba(255,255,255,.6);display:flex;align-items:center;justify-content:space-between;padding:0 22px}
.newsletter-field span{font-family:'Montserrat',sans-serif;font-size:14px;color:var(--white)}
.footer-links{left:0;width:1200px;top:3049px;display:flex;justify-content:center;gap:28px;font-family:'Montserrat',sans-serif;font-size:14px;color:var(--white)}
.footer-links i{font-style:normal;opacity:.7}
.bottom-bar{left:0;top:3128px;width:1200px;height:63px;background:var(--purple);display:flex;align-items:center;justify-content:space-between;padding:0 79px;color:var(--white);font-family:'Montserrat',sans-serif;font-size:14px}
.social{display:flex;gap:22px}
.social span{width:16px;height:16px;border-radius:50%;background:var(--white)}
</style>
</head>
<body>

<!-- hero -->
<div class="abs hero" role="img" aria-label="Dimmed photo of people working at a laptop with charts on paper"></div>
<header class="abs nav">
  <div class="abs logo">Kestrova.cz</div>
  <nav class="abs menu">
    <span class="active">HOME</span><span>ABOUT</span><span>SERVICES</span><span>BLOG</span><span>CONTACT</span>
  </nav>
</header>
<div class="abs hero-tag">Kestrova.cz</div>
<h1 class="abs hero-title">Lorem Ipsum is simply dummy.</h1>

<!-- contact callout -->
<div class="abs stack" style="left:122px;top:579px;width:978px;height:22px"></div>
<div class="abs callout" style="left:79px;top:598px;width:1042px;height:147px">
  <p>Contact us to get more information and<br>latest updates</p>
  <span class="btn" style="width:188px;height:47px">CONTACT US</span>
</div>

<!-- about -->
<div class="abs about-media" role="img" aria-label="Tablet with keyboard case showing the website home page"></div>
<h2 class="abs grad-title about-title">ABOUT US</h2>
<div class="abs about-copy">
  <p>Lorem Ipsum is simply dummy text of the printing and typesetting industry. Lorem Ipsum has been the industry's standard dummy text ever since the 1500s, when an unknown printer took a galley of type and scrambled it to make a type specimen book.</p>
  <p>It was popularised in the 1960s with the release of Vellmark sheets containing Lorem Ipsum passages, and more recently with desktop publishing software like Ornel PageCraft including versions of Lorem.</p>
</div>
<span class="abs btn" style="left:636px;top:1081px;width:198px;height:47px">KNOW MORE</span>

<!-- services -->
<div class="abs band"></div>
<h2 class="abs section-title" style="top:1272px">OUR SERVICES</h2>

<div class="abs service" style="left:70px;top:1344px">
  <svg width="96" height="96" viewBox="0 0 96 96" fill="none" stroke="#fff" stroke-width="2">
    <circle cx="48" cy="48" r="46" stroke-opacity=".9"/>
    <rect x="30" y="30" width="36" height="12" rx="2"/><rect x="30" y="46" width="36" height="12" rx="2"/>
    <line x1="36" y1="36" x2="50" y2="36"/><line x1="36" y1="52" x2="50" y2="52"/>
    <line x1="42" y1="62" x2="54" y2="62"/><line x1="48" y1="58" x2="48" y2="66"/>
  </svg>
  <h3>Data platform administration</h3>
  <p>Lorem Ipsum is simply dummy text of the<br>printing and typesetting industry.</p>
</div>
<div class="abs service" style="left:430px;top:1344px">
  <svg width="96" height="96" viewBox="0 0 96 96" fill="none" stroke="#fff" stroke-width="2">
    <circle cx="48" cy="48" r="46" stroke-opacity=".9"/>
    <rect x="38" y="24" width="20" height="40" rx="2"/>
    <line x1="42" y1="32" x2="54" y2="32"/><line x1="42" y1="40" x2="54" y2="40"/><line x1="42" y1="48" x2="54" y2="48"/>
    <rect x="26" y="44" width="10" height="20"/><rect x="60" y="44" width="10" height="20"/>
    <line x1="24" y1="68" x2="72" y2="68"/>
  </svg>
  <h3>Remote database</h3>
  <p>Lorem Ipsum is simply dummy text of the<br>printing and typesetting industry.</p>
</div>
<div class="abs service" style="left:792px;top:1344px">
  <svg width="96" height="96" viewBox="0 0 96 96" fill="none" stroke="#fff" stroke-width="2">
    <circle cx="48" cy="48" r="46" stroke-opacity=".9"/>
    <rect x="26" y="32" width="44" height="32" rx="2"/><line x1="26" y1="39" x2="70" y2="39"/>
    <polyline points="41,46 36,51 41,56"/><polyline points="55,46 60,51 55,56"/><line x1="50" y1="45" x2="46" y2="57"/>
  </svg>
  <h3>Development</h3>
  <p>Lorem Ipsum is simply dummy text of the<br>printing and typesetting industry.</p>
</div>
<div class="abs band-rule"></div>

<!-- team -->
<h2 class="abs section-title" style="top:1663px">OUR TEAM</h2>
<div class="abs member" style="left:79px;top:1728px">
  <div class="photo" role="img" aria-label="Portrait of a team member in a red top" style="background:linear-gradient(180deg,#f2f0f3 0%,#c98a74 55%,#9c2a2a 100%)"></div>
  <h4>Name Surname</h4><p>Lorem Ipsum is simply dummy.</p>
</div>
<div class="abs member" style="left:347px;top:1728px">
  <div class="photo" role="img" aria-label="Portrait of a team member in a dark sweater" style="background:linear-gradient(180deg,#f0eef2 0%,#c49a82 45%,#1f2e3c 100%)"></div>
  <h4>Name Surname</h4><p>Lorem Ipsum is simply dummy.</p>
</div>
<div class="abs member" style="left:615px;top:1728px">
  <div class="photo" role="img" aria-label="Portrait of a team member in a red blouse" style="background:linear-gradient(180deg,#f3f1f4 0%,#a9745e 45%,#c0302a 100%)"></div>
  <h4>Name Surname</h4><p>Lorem Ipsum is simply dummy.</p>
</div>
<div class="abs member" style="left:883px;top:1728px">
  <div class="photo" role="img" aria-label="Portrait of a team member in a black shirt" style="background:linear-gradient(180deg,#f1f0f3 0%,#b88d76 42%,#17171a 100%)"></div>
  <h4>Name Surname</h4><p>Lorem Ipsum is simply dummy.</p>
</div>
<span class="abs btn" style="left:506px;top:2115px;width:188px;height:45px">VIEW ALL</span>

<!-- blog -->
<h2 class="abs grad-title" style="left:0;width:1200px;top:2229px;text-align:center">LATEST BLOG</h2>
<div class="abs post" style="left:79px;top:2294px">
  <div class="img" role="img" aria-label="Business meeting around a table with printed charts" style="background:linear-gradient(135deg,#dfe7f0 0%,#8aa3bd 50%,#3b5f8a 100%)"></div>
  <div class="date">29 May 2018</div>
  <p>Lorem Ipsum is simply dummy text of the printing and typesetting.</p>
</div>
<div class="abs post" style="left:438px;top:2294px">
  <div class="img" role="img" aria-label="Hand pointing at a tablet showing a bar chart" style="background:linear-gradient(135deg,#5a6470 0%,#a9b6c4 50%,#e4e9ee 100%)"></div>
  <div class="date">29 May 2018</div>
  <p>Lorem Ipsum is simply dummy text of the printing and typesetting.</p>
</div>
<div class="abs post" style="left:800px;top:2294px">
  <div class="img" role="img" aria-label="Person typing on a laptop with data on screen" style="background:linear-gradient(135deg,#e2e4e8 0%,#6d7380 50%,#2a2d35 100%)"></div>
  <div class="date">29 May 2018</div>
  <p>Lorem Ipsum is simply dummy text of the printing and typesetting.</p>
</div>

<!-- footer -->
<div class="abs footer-bg" role="img" aria-label="Dimmed photo of hands working on a laptop"></div>
<div class="abs" style="left:122px;top:2819px;width:978px;height:16px;background:rgba(255,255,255,.22)"></div>
<div class="abs callout" style="left:79px;top:2675px;width:1042px;height:144px;padding-left:32px;padding-right:32px">
  <p>Download documents and &nbsp;presentations</p>
  <span class="btn" style="width:290px;height:50px">DOWNLOAD NOW
    <svg width="22" height="22" viewBox="0 0 22 22" fill="none" stroke="#fff" stroke-width="2.2"><line x1="11" y1="2" x2="11" y2="14"/><polyline points="6,9 11,14 16,9"/><polyline points="2,15 2,20 20,20 20,15"/></svg>
  </span>
</div>

<h2 class="abs section-title" style="top:2887px">NEWSLETTER</h2>
<div class="abs newsletter-field">
  <span>Enter your email</span>
  <svg width="26" height="24" viewBox="0 0 26 24"><path d="M1 11 L25 1 L17 23 L12 14 Z" fill="#7b52ff"/><path d="M12 14 L25 1" stroke="#2a2b31" stroke-width="1.2"/></svg>
</div>
<nav class="abs footer-links">
  <span>Home</span><i>|</i><span>About</span><i>|</i><span>Services</span><i>|</i><span>Blog</span><i>|</i><span>Contact</span>
</nav>
<div class="abs bottom-bar">
  <span>©Kestrova.cz- 2018. All Rights Reserved.</span>
  <div class="social"><span></span><span></span><span></span></div>
</div>

</body>
</html>
```